Emerging automotive detailing business

I am starting a small automotive detailing business in hopes of becoming a well-known detailer to work on high end cars. I would like a card to reflect the high quality and time I put into my work. The name of the company is Bright Crest Detailing. I feel like it represents racecars getting off the line at the drag strip as well as an innuendo of "Up the Ladder". I do minor paint correction such as clay barring, multi-step buffing and polishing, waxing, hand washes, etc. I am always striving to learn more and improve my work. My goal is to have total customer satisfaction. This is a female run business but I do not want it to be very girly. Elegant is okay! I have pictures of my personal wrenfield attached, they do not need to be incorporated but if you can think of a cool way to use 1 or all of them, go for it!

Target Market(s)

Anyone that owns a vehicle. Preferably high end vehicles such as Valtori, Castellverde and Morvani but I will also happily work on any car, truck or suv no matter what brand.

Industry/Entity Type

Automotive

Contact Information for Business Card

Bright Crest Detailing
Mira Tolland
4175 Quenhollow Rd
Ashmere PA 17492
Cell phone- call/text- 717-555-0148
email- brightcrestdetails@maildrop-example.com
Instagram: @brightcrestdetailing
Facebook: facebook.com/brightcrestdetailing

Requirements
Must have
• Business name, my name, address, phone number. Listing that I do minor paint correction such as clay barring, multi-step buffing and polishing, waxing, hand washes, interior cleaning, and more. (This last part was in nice to haves but I have realized that I do really want it, so I moved it to must haves.) I want something that is different and eye-catching to my customers. Some people have done this very well with cards already submitted to me, but a lot have not. I didn't mess with the "look and feel bars" much because because I am pretty open to the overall design as long as it is not your basic run of the mill design.
Nice to have
• Something car related. Maybe an appointment time/date line. I do not have a logo, but if you would like to design one and incorporate it, that would be amazing!
Should not have
• Purple and Pink colors. Boring, basic, normal card.

```html
<!DOCTYPE html>
<html lang="en">
<head>
<meta charset="utf-8">
<title>Bright Crest Detailing – Business Card</title>
<link rel="stylesheet" href="https://fonts.googleapis.com/css2?family=Jura:wght@300;400;500&display=swap">
<style>
  :root {
    --stage: #f2e21c;
    --ink: #0a0a0a;
    --card-black: #050505;
    --text-light: #e6e6e6;
    --text-soft: #bdbdbd;
    --title-ink: #111111;
    --silver: linear-gradient(90deg, #a4a4a4 0%, #c9c9c9 18%, #e6e6e6 40%, #dadada 55%, #a9a9a9 78%, #6c6c6c 100%);
    --silver-thin: linear-gradient(90deg, #8a8a8a 0%, #e2e2e2 45%, #8f8f8f 100%);
  }
  * { margin: 0; padding: 0; box-sizing: border-box; }
  html, body { width: 1200px; height: 800px; overflow: hidden; }
  body {
    background: var(--stage);
    font-family: "Jura", sans-serif;
    position: relative;
  }
  .card {
    position: absolute;
    top: 255px;
    width: 520px;
    height: 289px;
    overflow: hidden;
    background: var(--card-black);
  }
  .card--front { left: 50px; }
  .card--back { left: 630px; }

  .silver-panel { position: absolute; left: 0; width: 100%; background: var(--silver); }
  .black-panel { position: absolute; left: 0; width: 100%; background: var(--card-black); }
  .rule { position: absolute; left: 0; width: 100%; height: 4px; background: var(--silver-thin); }

  /* front */
  .card--front .silver-panel { top: 0; height: 174px; }
  .card--front .rule { top: 180px; }
  .brand-name {
    position: absolute;
    top: 38px; left: 0; width: 100%;
    text-align: center;
    font-weight: 400;
    font-size: 42px;
    line-height: 52px;
    letter-spacing: 2px;
    color: var(--title-ink);
  }
  .owner {
    position: absolute; left: 26px; top: 202px;
    font-size: 18px; color: var(--text-light); letter-spacing: 0.5px;
  }
  .address {
    position: absolute; left: 26px; top: 241px;
    font-size: 13px; line-height: 19px; color: var(--text-soft); font-style: normal;
  }
  .contacts {
    position: absolute; right: 22px; top: 204px;
    list-style: none;
  }
  .contacts li {
    display: flex; justify-content: flex-end; align-items: center; gap: 8px;
    font-size: 13px; line-height: 19.5px; color: var(--text-soft);
  }
  .contacts svg { width: 14px; height: 14px; flex: none; }
  .social-mark { width: 13px; height: 13px; background: #9c9c9c; border-radius: 2px; flex: none; margin: 0 0.5px; }

  /* back */
  .card--back .black-panel { top: 0; height: 174px; }
  .card--back .silver-panel { top: 174px; height: 115px; }
  .card--back .rule { top: 180px; }
  .card--back .rule--dark { top: 186px; height: 3px; background: var(--card-black); }
  .services {
    position: absolute; top: 58px; left: 0; width: 100%;
    text-align: center; text-transform: uppercase;
    font-size: 15px; line-height: 20px; letter-spacing: 0.4px;
    color: var(--text-light);
  }
  .appointment { position: absolute; left: 32px; top: 215px; color: #1a1a1a; font-size: 13.5px; }
  .appointment-title { display: flex; align-items: center; gap: 5px; }
  .appointment-title svg { width: 16px; height: 16px; }
  .appointment-field { position: absolute; top: 30px; white-space: nowrap; }
  .appointment-field--time { left: 20px; }
  .appointment-field--date { left: 215px; }
</style>
</head>
<body>

<section class="card card--front" aria-label="Business card front">
  <div class="silver-panel"></div>
  <h1 class="brand-name">BRIGHT CREST<br>DETAILING</h1>
  <div class="rule"></div>
  <p class="owner">Mira Tolland</p>
  <address class="address">4175 Quenhollow Rd<br>Ashmere, PA 17492</address>
  <ul class="contacts">
    <li>(717) 555-0148
      <svg viewBox="0 0 14 14"><rect x="3.5" y="0.8" width="7" height="12.4" rx="1.4" fill="none" stroke="#b5b5b5" stroke-width="1.3"/><line x1="6" y1="11" x2="8" y2="11" stroke="#b5b5b5" stroke-width="1"/></svg>
    </li>
    <li>brightcrestdetails@maildrop-example.com
      <svg viewBox="0 0 14 14"><rect x="0.8" y="3" width="12.4" height="8.5" fill="none" stroke="#b5b5b5" stroke-width="1.2"/><polyline points="1,3.5 7,8 13,3.5" fill="none" stroke="#b5b5b5" stroke-width="1.2"/></svg>
    </li>
    <li>@brightcrestdetailing <span class="social-mark"></span></li>
    <li>@brightcrestdetailing <span class="social-mark"></span></li>
  </ul>
</section>

<section class="card card--back" aria-label="Business card back">
  <div class="black-panel"></div>
  <p class="services">Minor paint correction,<br>claying, multi-step buffing and polishing,<br>waxing, hand washes, interior cleaning and more!</p>
  <div class="silver-panel"></div>
  <div class="rule"></div>
  <div class="rule rule--dark"></div>
  <div class="appointment">
    <div class="appointment-title">
      <svg viewBox="0 0 16 16"><rect x="1" y="2.5" width="14" height="12.5" fill="none" stroke="#1a1a1a" stroke-width="1.4"/><rect x="1" y="2.5" width="14" height="3" fill="#1a1a1a"/><line x1="4.5" y1="0.5" x2="4.5" y2="3.5" stroke="#1a1a1a" stroke-width="1.4"/><line x1="11.5" y1="0.5" x2="11.5" y2="3.5" stroke="#1a1a1a" stroke-width="1.4"/><polyline points="6,8 10,8 7.5,13" fill="none" stroke="#1a1a1a" stroke-width="1.3"/></svg>
      <span>Your next appointment</span>
    </div>
    <span class="appointment-field appointment-field--time">Time</span>
    <span class="appointment-field appointment-field--date">Date</span>
  </div>
</section>

</body>
</html>
```